IT Consultancy Needs Daring Webpage (uncoded)

We are looking for a web page for a small IT firm, Harbor Linkworks. We provide remote IT services, website development and IT consultancy. We are looking for a website that is a bit unique and will look both professional and cutting edge.

We are mainly targeting high cash flow small businesses.
Feel free to play with our yellow/blue theme. We where aiming for similar colours to movie posters i.e the Crimson Ledger, http://qlink.example/x4mTz. Think metallic, flashy and classy like a colourful Zuno.
Updates

We have a website but it is very poor and we would prefer if you did not use it for inspiration.

We quite like this design http://gallery.artfoldex.net/designs/web/?order=24&offset=24#/k7p3wq9

The three cornerstones of our business are Consult, Support and E-Marketing

other designs are welcome as well (different from the the link above)

Target Market(s)

Small Businesses

Industry/Entity Type

Movie

Requirements
Must have
• Space for Home, Services, Contact and Blog menu bars.

Our logo is ok, you are welcome to adjust it a little to meet your needs.

While we appreciate most websites have a dense middle ground for navigation panels, we would like the most important buttons highlighted as well as a slightly interesting background for example, instead of a plain colour background, a slight hint of a pattern or image.
Should not have
• Should not have a banner.

```html
<!DOCTYPE html>
<html lang="en">
<head>
<meta charset="utf-8">
<title>Harbor Linkworks</title>
<link rel="stylesheet" href="https://fonts.googleapis.com/css2?family=Archivo+Black&family=Ubuntu:wght@300;400;500;700&family=Arimo:wght@400;700&display=swap">
<style>
:root{
  --sun-light:#fdf1b4;
  --sun-mid:#fbd85a;
  --sun-deep:#f4b41e;
  --ink:#0d0d0d;
  --nav-top:#38a7e6;
  --nav-bottom:#0f73c0;
  --sea-top:#5ab6ea;
  --sea-bottom:#1a6fb6;
  --card-yellow-top:#ffe21a;
  --card-yellow-bottom:#ffb300;
  --card-blue-top:#a9dcf8;
  --card-blue-bottom:#3aa8e8;
  --card-edge-yellow:#f0a400;
  --card-edge-blue:#7cc8f2;
  --pill-top:#5bb8f5;
  --pill-bottom:#1a79d2;
  --footer:#000;
  --accent-blue:#22a2ea;
  --white:#fff;
}
*{box-sizing:border-box;margin:0;padding:0}
html,body{width:1200px;height:836px;overflow:hidden;background:#000}
.page{position:relative;width:1200px;height:836px;overflow:hidden;font-family:"Arimo",Arial,sans-serif;color:var(--ink)}

/* header */
.masthead{position:absolute;left:0;top:0;width:1200px;height:256px;
  background:radial-gradient(ellipse 520px 300px at 120px 110px,var(--sun-deep) 0%,var(--sun-mid) 45%,transparent 80%),
             linear-gradient(90deg,var(--sun-mid) 0%,var(--sun-light) 55%,var(--sun-mid) 100%)}
.brand{position:absolute;left:37px;top:23px;display:flex;align-items:center}
.brand-dot{width:176px;height:153px;border-radius:50%;background:var(--ink);border:5px solid var(--accent-blue)}
.brand-name{position:absolute;left:241px;top:76px;font-family:"Archivo Black",Arial,sans-serif;font-size:52px;line-height:1;color:var(--ink);white-space:nowrap}

.helpdesk{position:absolute;left:811px;top:91px}
.helpdesk-portrait{position:absolute;left:0;top:0;width:112px;height:112px;border-radius:50%;
  background:radial-gradient(circle at 50% 45%,#e9b48f 0%,#b8765a 55%,#6a4030 100%);border:4px solid var(--white);z-index:2}
.helpdesk-pill{position:absolute;left:100px;top:38px;width:222px;height:44px;border-radius:22px;
  background:linear-gradient(var(--pill-top),var(--pill-bottom));color:var(--white);font-family:"Ubuntu",sans-serif;font-weight:700;font-size:18px;line-height:44px;padding-left:38px}
.helpdesk-phone{position:absolute;left:107px;top:96px;font-family:"Arimo",Arial,sans-serif;font-size:28px;letter-spacing:1px;color:var(--ink);white-space:nowrap}

.mainnav{position:absolute;left:0;top:203px;width:602px;height:52px}
.mainnav svg{position:absolute;left:0;top:0}
.mainnav ul{position:relative;list-style:none;display:flex;align-items:center;height:52px;font-family:"Ubuntu",sans-serif;font-weight:300;font-size:19px;color:var(--ink)}
.mainnav li{position:absolute;top:14px}

/* content */
.services{position:absolute;left:0;top:255px;width:1200px;height:445px;
  background:linear-gradient(var(--sea-top),var(--sea-bottom))}
.service{position:absolute;top:24px;width:368px;height:397px;padding:10px 11px}
.service--yellow{background:linear-gradient(var(--card-yellow-top),var(--card-yellow-bottom));border:1px solid var(--card-edge-yellow)}
.service--blue{background:linear-gradient(var(--card-blue-top),var(--card-blue-bottom));border:1px solid var(--card-edge-blue)}
.service h2{font-family:"Arimo",Arial,sans-serif;font-weight:700;font-size:28px;line-height:34px;margin:2px 0 0 1px}
.service-visual{width:345px;height:164px;margin-top:13px;border:1px solid #222;
  background:radial-gradient(circle at 55% 60%,#9fd2e0 0%,#3e7f94 30%,#1b2630 65%,#0e1014 100%)}
.service p{font-size:13px;line-height:19px;margin:12px 4px 0;height:95px;overflow:hidden}
.read-more{position:absolute;left:16px;top:353px;width:98px;height:24px;border-radius:5px;background:linear-gradient(#3a3a3a,#050505);
  color:var(--white);font-size:13px;font-weight:700;line-height:24px;padding-left:9px}
.read-more svg{position:absolute;right:8px;top:8px}

/* footer */
.site-footer{position:absolute;left:0;top:700px;width:1200px;height:136px;background:var(--footer);color:var(--white);border-top:2px solid #1e7ac0}
.footer-name{position:absolute;left:13px;top:31px;font-weight:700;font-size:19px;color:var(--accent-blue);letter-spacing:.5px}
.footer-contact{position:absolute;left:13px;top:62px;font-size:13px;font-weight:700;line-height:18px}
.footer-contact b{color:var(--accent-blue)}
.footer-links{position:absolute;right:68px;top:60px;font-size:13px;text-align:right;line-height:21px}
.footer-links .sep{margin:0 10px}
</style>
</head>
<body>
<div class="page">
  <header class="masthead">
    <div class="brand"><span class="brand-dot"></span></div>
    <div class="brand-name">Harbor Linkworks</div>

    <div class="helpdesk">
      <div class="helpdesk-portrait" role="img" aria-label="Portrait of a support agent wearing a headset"></div>
      <div class="helpdesk-pill">CAN WE HELP YOU?</div>
      <div class="helpdesk-phone">0491 552 318</div>
    </div>

    <nav class="mainnav">
      <svg width="602" height="52" viewBox="0 0 602 52" aria-hidden="true">
        <defs><linearGradient id="navFill" x1="0" y1="0" x2="0" y2="1"><stop offset="0" stop-color="#3aa9e8"/><stop offset="1" stop-color="#0f72bf"/></linearGradient></defs>
        <path d="M0 0 H540 Q552 0 560 8 L602 52 H0 Z" fill="url(#navFill)"/>
      </svg>
      <ul>
        <li style="left:20px">Home</li>
        <li style="left:108px">I</li>
        <li style="left:156px">Services</li>
        <li style="left:262px">I</li>
        <li style="left:307px">Blog</li>
        <li style="left:384px">I</li>
        <li style="left:430px">Contact</li>
      </ul>
    </nav>
  </header>

  <main class="services">
    <article class="service service--yellow" style="left:13px">
      <h2>CONSULT</h2>
      <div class="service-visual" role="img" aria-label="Robotic hand touching a glowing digital globe"></div>
      <p>Lorem ipsum dolor sit amet, consectetur adipiscing elit. Aliquam mauris nulla, interdum sit amet tristique vitae, tristique vel sapien. Ut hendrerit mollis molestie. Donec a lectus tellus. Proin justo diam, semper et consectetur eu, consectetur ac velit. Curabitur viverra mollis lacus, et</p>
      <div class="read-more">read more<svg width="6" height="8" viewBox="0 0 6 8"><path d="M0 0 L6 4 L0 8Z" fill="#fff"/></svg></div>
    </article>
    <article class="service service--blue" style="left:418px">
      <h2>SUPPORT</h2>
      <div class="service-visual" role="img" aria-label="Robotic hand touching a glowing digital globe"></div>
      <p>Lorem ipsum dolor sit amet, consectetur adipiscing elit. Aliquam mauris nulla, interdum sit amet tristique vitae, tristique vel sapien. Ut hendrerit mollis molestie. Donec a lectus tellus. Proin justo diam, semper et consectetur eu, consectetur ac velit. Curabitur viverra mollis lacus, et</p>
      <div class="read-more">read more<svg width="6" height="8" viewBox="0 0 6 8"><path d="M0 0 L6 4 L0 8Z" fill="#fff"/></svg></div>
    </article>
    <article class="service service--yellow" style="left:822px">
      <h2>E MARKETING</h2>
      <div class="service-visual" role="img" aria-label="Robotic hand touching a glowing digital globe"></div>
      <p>Lorem ipsum dolor sit amet, consectetur adipiscing elit. Aliquam mauris nulla, interdum sit amet tristique vitae, tristique vel sapien. Ut hendrerit mollis molestie. Donec a lectus tellus. Proin justo diam, semper et consectetur eu, consectetur ac velit. Curabitur viverra mollis lacus, et</p>
      <div class="read-more">read more<svg width="6" height="8" viewBox="0 0 6 8"><path d="M0 0 L6 4 L0 8Z" fill="#fff"/></svg></div>
    </article>
  </main>

  <footer class="site-footer">
    <div class="footer-name">HARBOR LINKWORKS</div>
    <div class="footer-contact">
      <div><b>Tel :</b> +0491 552 318</div>
      <div><b>Office Hours :</b> 9.00 am till 5.30 pm</div>
    </div>
    <div class="footer-links">
      <div>Privacy Policy<span class="sep">|</span>Sitemap</div>
      <div>© 2011 harborlinkworks.example | All rights reserved</div>
    </div>
  </footer>
</div>
</body>
</html>
```